Velmaro Partners Logo and Business Card Design

We already have the rough logo shape (however please make the lines on the logo much thicker so a dark background is not required to see it) . see photos uploaded.
It needs to be refined with color and digitized and then have a front and back business card layout done.
The services are high vibration healing support through a therapy and feng shui service offering. We want people to Feel Happiness, Feel Prosperity and Feel Peace. (the back of the card would have these phrases on it) So a warm, calm and peaceful feeling card.
We would like the card to use the logo provided (with thicker lines and color added) but below the graphic please use the name "Velmaro Partners" NOT Velmaro.
We also would like to use the colors in the colorized matrix shown in photos (gold and purple) but on the lighter side. Thanks for your time!

Front of Card should include: Logo, with Company Name: Velmaro Partners as part of logo, Name: Tomas Brekke email: tomas@velmaro.example web: www.velmaro.example mobile: 555.018.2264 at bottom of front list Family Constellation | Feng Shui

Back of Card should have the logo and the following listed vertically:

PERSONAL | BUSINESS (Larger size then smaller bullet items below)
*Find Happiness
*Find Prosperity
*Find Peace

Target Market(s)

Target market is both business and personal

Contact Information for Business Card

Front of Card should include: Logo, with Company Name: Velmaro Partners as part of logo, Name: Tomas Brekke email: tomas@velmaro.example web: www.velmaro.example mobile: 555.018.2264 at bottom of front list Family Constellation | Feng Shui ++++ Back of Card should have the logo and the following listed vertically: PERSONAL | BUSINESS (Larger size then smaller bullet items below) *Find Happiness *Find Prosperity *Find Peace

Font styles to use
Sans Serif

Colors

Designer to choose colors to be used in the design.

Requirements
Nice to have
• Nice light contrast color for the back of card background
Should not have
• No dark colored background on Card.

```html
<!DOCTYPE html>
<html lang="en">
<head>
<meta charset="utf-8">
<title>Velmaro Partners Business Cards</title>
<link rel="stylesheet" href="https://fonts.googleapis.com/css2?family=Montserrat:wght@400;500;600;700&display=swap">
<style>
  :root {
    --bg: #3b322d;
    --gold: #d8ad2c;
    --gold-band: #e8bd2f;
    --purple: #7b62b8;
    --purple-faint: #eeebf7;
    --ink: #2a2a2a;
    --ink-soft: #4a4540;
    --card-white: #ffffff;
    --card-cream: #f8f4ea;
  }
  * { margin: 0; padding: 0; box-sizing: border-box; }
  html, body { width: 1200px; height: 786px; overflow: hidden; }
  body {
    background: var(--bg);
    font-family: "Montserrat", sans-serif;
    position: relative;
  }
  .card {
    position: absolute;
    top: 238px;
    width: 540px;
    height: 310px;
    border-radius: 4px;
    overflow: hidden;
    box-shadow: 0 10px 30px rgba(0,0,0,0.35);
  }
  .logo { text-align: center; }
  .logo-circle {
    border-radius: 50%;
    border: 5px solid var(--purple);
    margin: 0 auto;
  }
  .logo-name {
    font-weight: 600; color: var(--gold);
    line-height: 1;
  }
  .logo-sub {
    color: var(--ink-soft); font-weight: 500; line-height: 1;
  }

  /* Front */
  .card-front { left: 40px; background: var(--card-white); }
  .front-watermark {
    position: absolute; left: -40px; top: 70px;
    width: 160px; height: 160px; border-radius: 50%;
    border: 10px solid var(--purple-faint);
  }
  .front-logo { position: absolute; right: 52px; top: 16px; }
  .front-logo .logo-circle { width: 52px; height: 52px; margin-bottom: 8px; }
  .front-logo .logo-name { font-size: 34px; letter-spacing: 5px; }
  .front-logo .logo-sub { font-size: 12px; letter-spacing: 4px; margin-top: 6px; }
  .front-rule {
    position: absolute; left: 40px; right: 40px; top: 166px;
    height: 1px; background: var(--gold);
  }
  .person { position: absolute; left: 42px; top: 178px; }
  .person-name {
    font-weight: 700; color: var(--gold);
    font-size: 21px; letter-spacing: 1px; line-height: 1.1;
  }
  .person-role { font-size: 13px; color: var(--ink); margin-bottom: 6px; }
  .contact-list { list-style: none; font-size: 13px; color: var(--ink); line-height: 1.35; }
  .contact-list li { display: flex; align-items: center; gap: 8px; }
  .contact-list svg { width: 11px; height: 11px; fill: var(--gold); flex: none; }
  .front-bands { position: absolute; left: 0; bottom: 0; width: 540px; height: 62px; }
  .services {
    position: absolute; right: 20px; bottom: 28px;
    font-size: 12.5px; color: var(--ink); font-weight: 500;
  }

  /* Back */
  .card-back {
    left: 620px; background: var(--card-cream);
    display: flex; flex-direction: column; align-items: center; justify-content: center;
  }
  .back-logo .logo-circle { width: 66px; height: 66px; margin-bottom: 14px; }
  .back-logo .logo-name { font-size: 44px; letter-spacing: 6px; }
  .back-logo .logo-sub { font-size: 15px; letter-spacing: 3px; margin-top: 8px; }
  .segments {
    margin-top: 14px; background: var(--gold-band); color: var(--ink);
    font-weight: 700; font-size: 13px; letter-spacing: 0.5px;
    padding: 3px 14px; border-radius: 12px;
  }
  .promises {
    margin-top: 10px; color: var(--ink-soft); font-size: 12px;
    display: flex; gap: 8px; align-items: center;
  }
  .promises .dot { color: var(--gold); }
</style>
</head>
<body>
  <section class="card card-front">
    <div class="front-watermark"></div>
    <div class="logo front-logo">
      <div class="logo-circle"></div>
      <div class="logo-name">VELMARO</div>
      <div class="logo-sub">PARTNERS</div>
    </div>
    <div class="front-rule"></div>
    <div class="person">
      <div class="person-name">TOMAS BREKKE</div>
      <div class="person-role">Owner</div>
      <ul class="contact-list">
        <li><svg viewBox="0 0 12 12"><path d="M2 1h3l1 3-1.5 1a7 7 0 0 0 2.5 2.5L8 6l3 1v3a1 1 0 0 1-1 1A9 9 0 0 1 1 2a1 1 0 0 1 1-1z"/></svg>555.018.2264</li>
        <li><svg viewBox="0 0 12 12"><path d="M0 2h12v8H0z M1 3l5 4 5-4" /></svg>tomas@velmaro.example</li>
        <li><svg viewBox="0 0 12 12"><circle cx="6" cy="6" r="5.5"/></svg>www.velmaro.example</li>
      </ul>
    </div>
    <svg class="front-bands" viewBox="0 0 540 62" aria-hidden="true">
      <path d="M0 40 H250 L245 49 H0 Z" fill="var(--purple)"/>
      <path d="M300 0 H540 V62 H0 V54 H254 Q272 54 277 40 L284 12 Q288 0 300 0 Z" fill="var(--gold-band)"/>
      <rect x="0" y="57" width="540" height="5" fill="var(--card-white)"/>
    </svg>
    <div class="services">Family Constellation | Feng Shui</div>
  </section>

  <section class="card card-back">
    <div class="logo back-logo">
      <div class="logo-circle"></div>
      <div class="logo-name">VELMARO</div>
      <div class="logo-sub">PARTNERS</div>
    </div>
    <div class="segments">PERSONAL | BUSINESS</div>
    <div class="promises">
      <span>Find Happiness</span><span class="dot">•</span>
      <span>Find Prosperity</span><span class="dot">•</span>
      <span>Find Peace</span>
    </div>
  </section>
</body>
</html>
```